Online media outlet needs a blog and logo

A new online blog platform is being established in the UK. The blog will be very similar in layout to www.quorvel.co. It will need to have a main story slider showing three slides and block tiles beneath the slider for additional tiles.

The blog platform will be called 'Tandrel Brisk' and will also need a professional looking logo design for the name.

The website should be designed in Word Press.

Industry/Entity Type

Media

Logo Text

Tandrel Brisk

Coding

Coded - Design and coding required

Number of Pages Required

3 page

Font styles to use
Other font styles liked:
• Helvetica

Requirements
Must have
• A slider showing three slides. Be similar to Quor V (see previous comment). Be Word Press compatible.

```html
<!DOCTYPE html>
<html lang="en">
<head>
<meta charset="utf-8">
<title>Tandrel Brisk</title>
<link href="https://fonts.googleapis.com/css2?family=Roboto:wght@300;400;500;700&display=swap" rel="stylesheet">
<style>
:root{
  --blue:#1f6fc4;
  --blue-dark:#14519a;
  --navy:#0f3a78;
  --navy-deep:#0a2b5c;
  --ink:#222;
  --muted:#8a8a8a;
  --grey-band:#ececec;
  --white:#fff;
}
*{box-sizing:border-box;margin:0;padding:0}
html,body{width:1200px;height:2960px;overflow:hidden}
body{font-family:'Roboto',Helvetica,Arial,sans-serif;color:var(--ink);background:var(--white);position:relative}
.wrap{width:1000px;margin:0 auto;position:relative}

.topbar{height:30px;border-bottom:1px solid #e4e4e4;font-size:11px;color:#666}
.topbar .wrap{display:flex;justify-content:flex-end;gap:26px;line-height:30px;padding-right:90px}

.masthead{height:110px}
.masthead .wrap{display:flex;align-items:center;justify-content:space-between;height:110px}
.brand{display:flex;align-items:center;gap:10px;font-weight:700;font-size:26px;color:var(--ink);letter-spacing:.5px}
.brand-dot{width:30px;height:30px;border-radius:50%;background:var(--ink)}
.mainnav{display:flex;gap:0}
.mainnav a{display:block;padding:0 22px;line-height:40px;font-size:12px;font-weight:500;color:#555;text-decoration:none;border-left:1px solid #e6e6e6}
.mainnav a:first-child{border-left:0}

.hero{height:480px;position:relative;background:linear-gradient(120deg,#2b2f3a 0%,#5a4a45 40%,#8a5a4c 70%,#b98a7a 100%);overflow:hidden}
.hero-art{position:absolute;inset:0}
.hero-copy{position:absolute;left:680px;top:150px;width:440px;color:var(--white)}
.hero-copy h1{font-size:46px;font-weight:700;letter-spacing:1px;margin-bottom:16px}
.hero-copy p{font-size:13px;line-height:1.6;opacity:.9;margin-bottom:22px}
.btn{display:inline-block;background:var(--blue);color:var(--white);font-size:12px;font-weight:500;padding:10px 22px;letter-spacing:.5px}
.hero-arrow{position:absolute;top:220px}

.tiles{background:var(--grey-band);height:700px;padding-top:80px}
.tile-grid{display:grid;grid-template-columns:repeat(3,324px);gap:28px 14px}
.tile{height:252px;position:relative;color:var(--white);overflow:hidden}
.tile .tag{position:absolute;left:10px;top:10px;background:rgba(0,0,0,.55);font-size:10px;font-weight:500;padding:3px 7px;letter-spacing:.5px}
.tile .cap{position:absolute;left:0;right:0;bottom:0;padding:14px;background:linear-gradient(transparent,rgba(0,0,0,.7))}
.tile h3{font-size:14px;font-weight:400;line-height:1.35;margin-bottom:8px}
.meta{font-size:11px;display:flex;gap:16px;opacity:.85}

.signup{height:320px;background:linear-gradient(90deg,#1b5eae,#2d7fd4);color:var(--white);text-align:center;padding-top:90px}
.signup h2{font-size:36px;font-weight:400;letter-spacing:1px;margin-bottom:10px}
.signup p{font-size:13px;opacity:.85;margin-bottom:22px}
.signup-form{display:flex;justify-content:center;gap:8px}
.field{width:270px;height:44px;background:var(--white);color:#999;font-size:12px;text-align:left;line-height:44px;padding-left:16px}
.signup .btn{height:44px;line-height:44px;padding:0 24px;background:var(--blue-dark)}

.latest{padding-top:50px;height:640px}
.section-title{font-size:24px;font-weight:500;margin-bottom:24px}
.latest-grid{display:flex;gap:40px}
.feature{width:460px}
.feature .thumb{height:210px;background:linear-gradient(135deg,#c9b8a6,#7e6a5c 60%,#3e3f4a);margin-bottom:16px}
.feature h3{font-size:18px;font-weight:500;margin-bottom:8px}
.feature .meta{color:var(--muted);opacity:1;margin-bottom:12px}
.feature p{font-size:12px;line-height:1.7;color:#666;margin-bottom:14px}
.more{font-size:12px;font-weight:700;color:var(--blue)}
.side-list{flex:1;display:flex;flex-direction:column;gap:26px}
.side-item{display:flex;gap:20px}
.side-item .thumb{width:180px;height:108px;flex:none}
.side-item h4{font-size:14px;font-weight:400;margin-bottom:6px}
.side-item p{font-size:11px;line-height:1.6;color:#888;margin-bottom:8px}
.side-item .meta{color:var(--muted);opacity:1;font-size:10px}

.tiles-lower{height:320px}

.footer{background:var(--navy);height:320px;color:var(--white);padding-top:40px}
.footer-grid{display:grid;grid-template-columns:280px 260px 270px 190px}
.footer h5{font-size:15px;font-weight:500;letter-spacing:.5px;margin-bottom:18px}
.tweet{display:flex;gap:10px;font-size:11px;line-height:1.5;margin-bottom:16px;padding-right:30px}
.tweet small{display:block;opacity:.6;font-size:10px}
.map{width:220px;height:140px;background:linear-gradient(135deg,#e8e6e0,#cfd6d2)}
.footer ul{list-style:none;font-size:12px}
.footer li{display:flex;gap:10px;align-items:center;margin-bottom:14px;opacity:.9}
.dot{width:18px;height:18px;border-radius:50%;border:1px solid rgba(255,255,255,.7);flex:none}
.copyright{position:absolute;left:0;right:0;top:2920px;height:40px;background:var(--navy-deep);color:rgba(255,255,255,.7);font-size:11px;text-align:center;line-height:40px}
</style>
</head>
<body>

<div class="topbar"><div class="wrap"><span>Advertise</span><span>Contact Us</span><span>Society</span></div></div>

<header class="masthead"><div class="wrap">
  <div class="brand"><span class="brand-dot"></span>TANDREL BRISK</div>
  <nav class="mainnav"><a>HOME</a><a>POLITICS</a><a>COMPETITION</a><a>SOCIETY</a><a>PRESS</a><a>INVESTMENT</a></nav>
</div></header>

<section class="hero">
  <div class="hero-art" role="img" aria-label="Speaker on stage addressing a seated conference audience"></div>
  <svg class="hero-arrow" style="left:40px" width="24" height="40" viewBox="0 0 24 40"><path d="M20 4 4 20l16 16" fill="none" stroke="#fff" stroke-width="3"/></svg>
  <svg class="hero-arrow" style="right:40px" width="24" height="40" viewBox="0 0 24 40"><path d="m4 4 16 16L4 36" fill="none" stroke="#fff" stroke-width="3"/></svg>
  <div class="hero-copy">
    <h1>TANDREL BRISK</h1>
    <p>Independent voices on politics, power and public life across Britain, with fresh analysis and debate delivered every day of the week.</p>
    <span class="btn">MORE INFO</span>
  </div>
</section>

<section class="tiles"><div class="wrap tile-grid">
  <article class="tile" role="img" aria-label="Desk with laptop and finance papers" style="background:linear-gradient(135deg,#6d7782,#2f3944)"><span class="tag">INVESTMENT</span><div class="cap"><h3>Nemo enim ipsam voluptatem quia voluptas sit aspernatur</h3><div class="meta"><span>March 25, 2016</span><span>2 comments</span></div></div></article>
  <article class="tile" role="img" aria-label="Government building with national flag" style="background:linear-gradient(135deg,#9fb4cf,#4f5d73)"><span class="tag">GOVERNMENT</span><div class="cap"><h3>Nemo enim ipsam voluptatem quia voluptas sit aspernatur</h3><div class="meta"><span>March 25, 2016</span><span>2 comments</span></div></div></article>
  <article class="tile" role="img" aria-label="Politician speaking at a podium" style="background:linear-gradient(135deg,#5a4a3a,#1e1a18)"><span class="tag">POLITICS</span><div class="cap"><h3>Nemo enim ipsam voluptatem quia voluptas sit aspernatur</h3><div class="meta"><span>March 25, 2016</span><span>2 comments</span></div></div></article>
  <article class="tile" role="img" aria-label="Colleagues talking in a bright office" style="background:linear-gradient(135deg,#d8d4cc,#8a7d70)"><span class="tag">CURRENT TOPICS</span><div class="cap"><h3>Nemo enim ipsam voluptatem quia voluptas sit aspernatur</h3><div class="meta"><span>March 25, 2016</span><span>2 comments</span></div></div></article>
  <article class="tile" role="img" aria-label="Businessman walking on a city road" style="background:linear-gradient(135deg,#c9b79a,#6a5a48)"><span class="tag">COMPETITION</span><div class="cap"><h3>Nemo enim ipsam voluptatem quia voluptas sit aspernatur</h3><div class="meta"><span>March 25, 2016</span><span>2 comments</span></div></div></article>
  <article class="tile" role="img" aria-label="Press photographers at a political event" style="background:linear-gradient(135deg,#4a4a4f,#16161a)"><span class="tag">POLITICS</span><div class="cap"><h3>Nemo enim ipsam voluptatem quia voluptas sit aspernatur</h3><div class="meta"><span>March 25, 2016</span><span>2 comments</span></div></div></article>
</div></section>

<section class="signup">
  <h2>TANDREL BRISK EMAIL</h2>
  <p>Get our best stories, debates and opinion pieces sent straight to your inbox.</p>
  <div class="signup-form"><span class="field">Your Name</span><span class="field">Your Email</span><span class="btn">SIGN UP</span></div>
</section>

<section class="latest"><div class="wrap">
  <h2 class="section-title">LATEST BLOG</h2>
  <div class="latest-grid">
    <article class="feature">
      <div class="thumb" role="img" aria-label="Woman working at a desk in an office, video post"></div>
      <h3>NEMO ENIM IPSAM VOLUPTATEM QUIA</h3>
      <div class="meta"><span>April 23, 2016</span><span>2 comments</span><span>3 hours ago</span></div>
      <p>Sed ut perspiciatis unde omnis iste natus error sit voluptatem accusantium doloremque laudantium, totam rem aperiam, eaque ipsa quae ab illo inventore veritatis et quasi architecto beatae vitae dicta sunt explicabo.</p>
      <span class="more">SHOW MORE ›</span>
    </article>
    <div class="side-list">
      <div class="side-item"><div class="thumb" role="img" aria-label="Hands over documents on a table" style="background:linear-gradient(135deg,#c7b9a5,#7b6c5c)"></div><div><h4>Nemo enim ipsam voluptatem quia</h4><p>Sed ut perspiciatis unde omnis iste natus error sit voluptatem accusantium.</p><div class="meta"><span>2 minutes ago</span><span>2 comments</span></div></div></div>
      <div class="side-item"><div class="thumb" role="img" aria-label="Crowd with umbrellas in the rain" style="background:linear-gradient(135deg,#5d6f86,#1f2834)"></div><div><h4>Nemo enim ipsam voluptatem quia</h4><p>Sed ut perspiciatis unde omnis iste natus error sit voluptatem accusantium.</p><div class="meta"><span>2 minutes ago</span><span>2 comments</span></div></div></div>
      <div class="side-item"><div class="thumb" role="img" aria-label="Business meeting around a table" style="background:linear-gradient(135deg,#b7c2cf,#4e5a6a)"></div><div><h4>Nemo enim ipsam voluptatem quia</h4><p>Sed ut perspiciatis unde omnis iste natus error sit voluptatem accusantium.</p><div class="meta"><span>2 minutes ago</span><span>2 comments</span></div></div></div>
      <div class="side-item"><div style="width:180px;flex:none"></div><div><h4>Nemo enim ipsam voluptatem quia</h4><p>Sed ut perspiciatis unde omnis iste natus error sit voluptatem accusantium.</p><div class="meta"><span>2 minutes ago</span><span>2 comments</span></div></div></div>
    </div>
  </div>
</div></section>

<section class="tiles-lower"><div class="wrap tile-grid">
  <article class="tile" role="img" aria-label="Activist climbing a wall" style="background:linear-gradient(135deg,#7a8896,#2d3640)"><span class="tag">CURRENT TOPICS</span><div class="cap"><h3>Nemo enim ipsam voluptatem quia voluptas sit aspernatur</h3><div class="meta"><span>March 25, 2016</span><span>2 comments</span></div></div></article>
  <article class="tile" role="img" aria-label="Shelves of archived files" style="background:linear-gradient(135deg,#a78a64,#4a3a2a)"><span class="tag">COMPETITION</span><div class="cap"><h3>Nemo enim ipsam voluptatem quia voluptas sit aspernatur</h3><div class="meta"><span>March 25, 2016</span><span>2 comments</span></div></div></article>
  <article class="tile" role="img" aria-label="Politician at a press conference" style="background:linear-gradient(135deg,#6a3a3a,#1a1414)"><span class="tag">POLITICS</span><div class="cap"><h3>Nemo enim ipsam voluptatem quia voluptas sit aspernatur</h3><div class="meta"><span>March 25, 2016</span><span>2 comments</span></div></div></article>
</div></section>

<footer class="footer"><div class="wrap footer-grid">
  <div>
    <h5>LATEST TWEET'S</h5>
    <div class="tweet"><span class="dot"></span><div>New column on the housing debate is now live, read it today <small>1 day ago</small></div></div>
    <div class="tweet"><span class="dot"></span><div>Our weekly politics roundup is out, join the discussion online <small>1 day ago</small></div></div>
  </div>
  <div>
    <h5>OUR LOCATION</h5>
    <div class="map" role="img" aria-label="Street map of the office location"></div>
  </div>
  <div>
    <h5>RECENT POSTS</h5>
    <ul>
      <li><span>›</span>Sed ut perspiciatis unde omnis</li>
      <li><span>›</span>Nemo enim ipsam voluptatem quia</li>
      <li><span>›</span>Lorem ipsum dolor sit amet</li>
      <li><span>›</span>Quis autem vel eum reprehenderit</li>
    </ul>
  </div>
  <div>
    <h5>SOCIAL</h5>
    <ul>
      <li><span class="dot"></span>Page</li>
      <li><span class="dot"></span>Feed</li>
      <li><span class="dot"></span>Circle</li>
      <li><span class="dot"></span>Channel</li>
    </ul>
  </div>
</div></footer>

<div class="copyright">Copyright 2016 | All Rights Reserved | Tandrel Brisk</div>

</body>
</html>
```